Coral Bay Pools New website

I currently operate a swimming pool service and repair business and looking for a re design for my website as it has been over 5 years since it was designed. current site is coralbaypoolslv.com

```html
<!DOCTYPE html>
<html lang="en">
<head>
<meta charset="utf-8">
<title>Coral Bay Pools</title>
<link href="https://fonts.googleapis.com/css2?family=Bodoni+Moda:wght@700;800&family=Montserrat:ital,wght@0,400;0,500;0,600;0,700;0,800;1,400&display=swap" rel="stylesheet">
<style>
:root{
  --blue:#0b5aa2;
  --blue-dark:#084a88;
  --orange:#f7a21b;
  --ink:#111111;
  --text:#3d3d3d;
  --pale:#e6f0fb;
  --line:#e3e3e3;
}
*{box-sizing:border-box;margin:0;padding:0}
html,body{width:1200px;height:5042px;overflow:hidden;background:#fff}
body{position:relative;font-family:'Montserrat',sans-serif;color:var(--text)}
.abs{position:absolute}
.serif{font-family:'Bodoni Moda',serif;font-weight:700;color:var(--ink)}
.eyebrow{position:absolute;font-size:22px;font-weight:500;color:var(--blue);letter-spacing:1px;display:flex;align-items:center;gap:12px}
.eyebrow::before{content:"";width:56px;height:2px;background:var(--orange)}
.eyebrow.both::after{content:"";width:56px;height:2px;background:var(--orange)}
.btn{position:absolute;background:var(--blue);color:#fff;font-weight:700;display:flex;align-items:center;justify-content:center;border-radius:14px 0 14px 0;box-shadow:-6px -6px 0 var(--orange)}
.photo{position:absolute}

/* header */
.nav{left:544px;top:33px;width:591px;height:46px;border:1.5px solid #7aa6cf;border-radius:23px;display:flex;align-items:center;justify-content:space-around;padding:0 10px;font-size:13px;font-weight:500;color:var(--ink);background:#fff}
.nav .active{background:var(--orange);color:#fff;font-weight:700;padding:8px 18px;border-radius:16px}
.logo{left:68px;top:0;width:274px;height:196px;background:#fff;border-radius:0 0 40px 40px;z-index:3;display:flex;align-items:center;justify-content:center;gap:10px;font-family:'Bodoni Moda',serif;font-weight:700;font-size:26px;color:var(--blue)}
.logo .dot{width:22px;height:22px;border-radius:50%;background:var(--orange)}

/* hero */
.hero{left:0;top:104px;width:1200px;height:790px;background:radial-gradient(ellipse at 70% 70%,#1f8fe0 0%,#0e4f8f 30%,#0a2446 60%,#050d1d 100%)}
.hero-title{left:70px;top:268px;color:#fff;line-height:1}
.hero-title .small{font-size:62px;display:block;color:#fff}
.hero-title .big{font-size:132px;display:block;color:#fff;margin-top:2px}
.hero-text{left:74px;top:462px;width:484px;color:#fff;font-size:18px;font-weight:600;line-height:30px;text-align:justify}

/* features */
.feature{position:absolute;top:990px;width:200px;text-align:center}
.feature .ring{width:126px;height:126px;margin:0 auto;border-radius:50%;border:4px solid var(--orange);background:var(--blue);display:flex;align-items:center;justify-content:center}
.feature h3{font-family:'Bodoni Moda',serif;font-weight:700;color:var(--ink);font-size:20px;line-height:24px;margin-top:20px}

/* about */
.about-h{left:84px;top:1322px;font-size:58px;line-height:66px}
.about-lead{left:82px;top:1470px;width:440px;font-size:16px;font-weight:700;color:var(--ink);line-height:26px}
.about-p{left:82px;top:1538px;width:440px;font-size:13px;line-height:27px;text-align:justify}
.pill{position:absolute;border-radius:150px}

/* services */
.sec-h{left:0;width:1200px;text-align:center;font-size:58px}
.sec-p{left:120px;top:2072px;width:960px;text-align:center;font-size:14.5px;line-height:26px;color:#222}
.card{position:absolute;top:2184px;width:342px;height:350px;border-radius:20px;overflow:hidden;background:#fff;box-shadow:0 4px 18px rgba(0,0,0,.12)}
.card .img{position:absolute;left:0;top:0;width:100%;height:282px}
.card h4{position:absolute;left:0;bottom:26px;width:100%;text-align:center;font-family:'Bodoni Moda',serif;font-size:22px;color:var(--ink)}
.card.feature-card .overlay{position:absolute;inset:0;color:#fff;text-align:center;padding:90px 28px 0}
.card.feature-card h5{font-family:'Bodoni Moda',serif;font-size:22px;font-weight:700;margin-bottom:14px}
.card.feature-card p{font-size:14px;line-height:27px}
.card.feature-card a{display:inline-block;margin-top:14px;font-size:14px;font-weight:700;text-decoration:underline;color:#fff}
.arrow{position:absolute;width:58px;height:58px;border-radius:50%;display:flex;align-items:center;justify-content:center}
.arrow.out{border:2px solid var(--orange);background:#fff}
.arrow.fill{background:var(--blue)}

/* testimonials */
.review{position:absolute;top:2818px;width:322px;height:252px;background:#fff;box-shadow:0 4px 18px rgba(0,0,0,.12);padding:34px 28px 0 26px}
.review p{font-size:13.5px;font-style:italic;line-height:24px;color:#444}
.review .who{position:absolute;left:26px;top:168px;display:flex;align-items:center;gap:16px}
.review .avatar{width:66px;height:66px;border-radius:50%;background:linear-gradient(135deg,#c99a78,#6e4b38)}
.review .name{font-size:18px;font-weight:700;color:var(--blue)}
.review .stars{color:var(--orange);font-size:13px;letter-spacing:1px}
.review .quote{position:absolute;right:22px;top:170px;font-family:'Bodoni Moda',serif;font-size:110px;line-height:110px;color:var(--blue);height:60px;overflow:hidden}

/* call band */
.call{left:68px;top:3233px;width:1065px;height:524px;border-radius:60px;overflow:hidden;background:linear-gradient(180deg,#cfe7f7 0%,#9fd0ef 34%,#2d8fd6 46%,#0d67b6 70%,#0a4f95 100%)}
.call-h{left:0;top:3528px;width:1200px;text-align:center;font-size:92px;color:#fff}
.call-phone{left:0;top:3652px;width:1200px;display:flex;justify-content:center;align-items:center;gap:20px;color:#fff;font-size:44px;font-weight:500}

/* contact */
.field{position:absolute;border:1px solid #dadada;background:#fff;font-size:13px;color:#999;padding:14px 20px}

/* footer */
.footer-bg{left:0;top:4660px;width:1200px;height:312px;background:var(--pale)}
.foot-h{font-family:'Bodoni Moda',serif;font-weight:700;font-size:18px;color:var(--ink)}
.foot-h::after{content:"";display:block;width:32px;height:2px;background:var(--orange);margin-top:8px}
.foot-list{list-style:none;font-size:13.5px;color:#222}
.foot-list li{display:flex;align-items:center;gap:14px;height:26px}
.foot-list li::before{content:"";width:7px;height:7px;border-radius:50%;background:var(--blue)}
.contact-row{position:absolute;left:568px;display:flex;gap:18px;font-size:13px;color:#222;line-height:17px}
.contact-row .ic{width:26px;height:26px;background:var(--blue);border-radius:5px;display:flex;align-items:center;justify-content:center;flex:none}
.bottom-bar{left:0;top:4971px;width:1200px;height:71px;background:var(--blue-dark)}
.social{position:absolute;top:4992px;width:26px;height:26px;border-radius:50%;background:var(--orange)}
</style>
</head>
<body>

<!-- hero -->
<div class="hero abs" role="img" aria-label="Night view of a lit resort swimming pool beside a villa and palm trees"></div>
<svg class="abs" style="left:0;top:760px" width="1200" height="150" viewBox="0 0 1200 150">
  <path d="M0,22 Q600,140 1200,16 L1200,150 L0,150 Z" fill="#fff"/>
  <path d="M0,18 Q600,128 1200,14 L1200,22 Q600,160 0,26 Z" fill="#f7a21b"/>
</svg>

<div class="logo abs"><span class="dot"></span>Coral Bay Pools</div>
<nav class="nav abs">
  <span class="active">HOME</span><span>ABOUT US</span><span>SERVICES</span><span>FREE ESTIMATE</span><span>CONTACT US</span>
</nav>

<h1 class="hero-title abs serif"><span class="small">CORAL BAY</span><span class="big">POOLS</span></h1>
<p class="hero-text abs">When you need professional pool cleaning services in Nevada, you can count on the professionals at Coral Bay Pools to provide you with superior and prompt solutions.</p>
<div class="btn" style="left:80px;top:624px;width:240px;height:72px;font-size:20px">FREE ESTIMATE</div>

<!-- features -->
<div class="feature" style="left:60px">
  <div class="ring"><svg width="60" height="60" viewBox="0 0 24 24" fill="none" stroke="#fff" stroke-width="2"><circle cx="12" cy="10" r="5"/><path d="M12 2v3M12 15v7M5 10H2M22 10h-3M7 5 5 3M17 5l2-2"/></svg></div>
  <h3>SERVICE AND<br>REPAIR</h3>
</div>
<div class="feature" style="left:268px">
  <div class="ring"><svg width="56" height="56" viewBox="0 0 24 24" fill="none" stroke="#fff" stroke-width="2"><rect x="3" y="4" width="16" height="16" rx="1"/><path d="M7 12l4 4 10-11"/></svg></div>
  <h3>WEEKLY<br>MAINTENANCE</h3>
</div>
<div class="feature" style="left:497px">
  <div class="ring"><svg width="58" height="58" viewBox="0 0 24 24" fill="none" stroke="#fff" stroke-width="2"><circle cx="12" cy="12" r="7"/><circle cx="12" cy="12" r="2.5"/><path d="M12 2v3M12 19v3M2 12h3M19 12h3M5 5l2 2M17 17l2 2M19 5l-2 2M5 19l2-2"/></svg></div>
  <h3>SCHEDULED<br>CLEANINGS</h3>
</div>
<div class="feature" style="left:724px">
  <div class="ring"><svg width="58" height="58" viewBox="0 0 24 24" fill="#fff"><circle cx="12" cy="8" r="3"/><circle cx="5.5" cy="10" r="2.3"/><circle cx="18.5" cy="10" r="2.3"/><path d="M7 20c0-4 2-7 5-7s5 3 5 7z"/><path d="M1.5 19c0-3 1.5-5.5 4-5.5 1 0 1.8.3 2.3.8C6.8 15.7 6.3 17.3 6.2 19z"/><path d="M22.5 19c0-3-1.5-5.5-4-5.5-1 0-1.8.3-2.3.8 1 1.4 1.5 3 1.6 4.7z"/></svg></div>
  <h3>EXCELLENT<br>WORKMANSHIP</h3>
</div>
<div class="feature" style="left:943px">
  <div class="ring"><svg width="60" height="60" viewBox="0 0 24 24" fill="none" stroke="#fff" stroke-width="1.8"><path d="M8 14V4h4M14 14V4M8 7h6M8 10h6"/><path d="M2 16c2-1.5 3-1.5 5 0s3 1.5 5 0 3-1.5 5 0 3 1.5 5 0M2 20c2-1.5 3-1.5 5 0s3 1.5 5 0 3-1.5 5 0 3 1.5 5 0"/></svg></div>
  <h3>HIGH LEVEL<br>OF CARE</h3>
</div>

<!-- about -->
<div class="eyebrow" style="left:88px;top:1290px">WHO WE ARE</div>
<h2 class="about-h abs serif">About Coral<br>Bay Pools</h2>
<p class="about-lead abs">We are a full service pool company servicing the Las Vegas Valley.</p>
<p class="about-p abs">My name is Marco and I'm the owner of Coral Bay Pools. I recently started this business in 2016 to provide Las Vegas with excellent, reliable pool service. Just because we are a new company that doesn't mean we lack experience. I've been in the pool industry for seven years and counting and have managed everything from your backyard pool to olympic sized pools with five plus years managing casino properties as well.</p>
<div class="btn" style="left:92px;top:1752px;width:178px;height:52px;font-size:16px">READ MORE</div>
<div class="pill photo" style="left:609px;top:1305px;width:276px;height:486px;background:linear-gradient(180deg,#4ea4e8 0%,#9fd1f0 25%,#2f7a3b 40%,#e8875a 60%,#f08a5c 100%)" role="img" aria-label="Resort pool with orange tiled deck and palm trees"></div>
<div class="pill photo" style="left:900px;top:1382px;width:215px;height:375px;background:linear-gradient(180deg,#4ea4e8 0%,#a8d7f2 25%,#2e7a3c 42%,#2ec3e6 62%,#1aa4d9 100%)" role="img" aria-label="Turquoise resort pool under blue sky"></div>

<!-- services -->
<div class="eyebrow both" style="left:456px;top:1945px">WHAT WE DO</div>
<h2 class="sec-h abs serif" style="top:1972px">Our Services</h2>
<p class="sec-p abs">When you invested in your pool, you knew it was a long-term investment in both money and time. At home, it's an oasis, a place to beat the heat and relax. At your business, it's both an accessory for the enjoyment of your clients as well as an important design element.</p>

<div class="card" style="left:67px">
  <div class="img" role="img" aria-label="Pool with lounge chairs and umbrellas" style="background:linear-gradient(180deg,#d9eef2 0%,#7cb583 30%,#38a7d8 60%,#2a3c4a 100%)"></div>
  <h4>POOL SERVICES</h4>
</div>
<div class="card feature-card" style="left:430px">
  <div class="img" role="img" aria-label="Blue commercial pool water" style="height:100%;background:linear-gradient(180deg,#2b7fc4,#1a67b0 60%,#155ea3)"></div>
  <div class="overlay">
    <h5>COMMERCIAL POOL</h5>
    <p>Lorem ipsum dolor sit amet, consecte tur adipiscing elit. Morbi id risus et eros malesuada eleifend.</p>
    <a>READ MORE</a>
  </div>
</div>
<div class="card" style="left:791px">
  <div class="img" role="img" aria-label="Residential pool with ladder beside buildings" style="background:linear-gradient(180deg,#c9cfd6 0%,#d0635a 30%,#5bb067 45%,#34c2e0 70%,#1ea6d2 100%)"></div>
  <h4>RESIDENTIAL POOL</h4>
</div>

<div class="arrow out" style="left:537px;top:2597px"><svg width="14" height="22" viewBox="0 0 14 22"><path d="M11 3 4 11l7 8" fill="none" stroke="#f7a21b" stroke-width="3"/></svg></div>
<div class="arrow fill" style="left:605px;top:2597px"><svg width="14" height="22" viewBox="0 0 14 22"><path d="M3 3l7 8-7 8" fill="none" stroke="#fff" stroke-width="3"/></svg></div>

<!-- testimonials -->
<div class="eyebrow" style="left:88px;top:2834px">CLIENT REVIEWS</div>
<h2 class="abs serif" style="left:90px;top:2862px;font-size:58px">Testimonials</h2>
<div class="arrow out" style="left:88px;top:3008px"><svg width="14" height="22" viewBox="0 0 14 22"><path d="M11 3 4 11l7 8" fill="none" stroke="#f7a21b" stroke-width="3"/></svg></div>
<div class="arrow fill" style="left:157px;top:3008px"><svg width="14" height="22" viewBox="0 0 14 22"><path d="M3 3l7 8-7 8" fill="none" stroke="#fff" stroke-width="3"/></svg></div>

<div class="review" style="left:458px">
  <p>Lorem ipsum dolor sit amet, consecte tur adipiscing elit. Pellentesque aliquet eros vitae placerat hendrerit. Maece nas maximus commodo sapien, vitae lobortis ligula</p>
  <div class="who"><div class="avatar" role="img" aria-label="Customer portrait"></div><div><div class="name">Daniel Reyes</div><div class="stars">★★★★★</div></div></div>
  <div class="quote">”</div>
</div>
<div class="review" style="left:810px">
  <p>Lorem ipsum dolor sit amet, consecte tur adipiscing elit. Pellentesque aliquet eros vitae placerat hendrerit. Maece nas maximus commodo sapien, vitae lobortis ligula</p>
  <div class="who"><div class="avatar" role="img" aria-label="Customer portrait"></div><div><div class="name">Priya Hart</div><div class="stars">★★★★★</div></div></div>
  <div class="quote">”</div>
</div>

<!-- call band -->
<div class="call abs" role="img" aria-label="Seaside infinity pool with umbrellas and lounge chairs"></div>
<h2 class="call-h abs serif">Call Us Today!</h2>
<div class="call-phone abs">
  <svg width="60" height="60" viewBox="0 0 60 60"><circle cx="30" cy="30" r="27" fill="none" stroke="#fff" stroke-width="3"/><path d="M22 17c2 0 4 5 4 6s-3 2-3 3c0 2 6 9 9 10 1 0 2-3 3-3s6 2 6 4c0 2-3 5-6 5-8 0-19-11-19-19 0-3 3-6 6-6z" fill="#fff"/></svg>
  <span>(702) 555-0148</span>
</div>

<!-- contact -->
<div class="pill photo" style="left:80px;top:4006px;width:220px;height:431px;background:linear-gradient(180deg,#dfe9f1 0%,#2f6b34 25%,#8a4f3a 45%,#1b8fd6 70%,#0d5fae 100%)" role="img" aria-label="Backyard pool beside a brick house"></div>
<div class="pill photo" style="left:311px;top:3930px;width:278px;height:485px;background:linear-gradient(180deg,#3e87d9 0%,#9bc6ef 25%,#9a5c48 45%,#3a7a3a 58%,#1a96dc 78%,#0d5fae 100%)" role="img" aria-label="Large home with pool and lounge chairs"></div>

<div class="eyebrow" style="left:656px;top:3916px">GET IN TOUCH</div>
<h2 class="abs serif" style="left:652px;top:3944px;font-size:58px">Contact Us</h2>
<div class="field" style="left:652px;top:4063px;width:221px;height:44px">First Name:</div>
<div class="field" style="left:892px;top:4063px;width:221px;height:44px">Last Name:</div>
<div class="field" style="left:652px;top:4127px;width:221px;height:44px">Phone:</div>
<div class="field" style="left:892px;top:4127px;width:221px;height:44px">Email:</div>
<div class="field" style="left:652px;top:4192px;width:461px;height:141px">Mesage:</div>
<div class="btn" style="left:660px;top:4372px;width:178px;height:52px;font-size:16px">SUBMIT NOW</div>

<!-- footer -->
<div class="footer-bg abs"></div>
<svg class="abs" style="left:0;top:4570px" width="1200" height="120" viewBox="0 0 1200 120">
  <path d="M0,112 Q600,0 1200,112 L1200,120 L0,120 Z" fill="#e6f0fb"/>
  <path d="M0,108 Q600,-8 1200,108 L1200,114 Q600,8 0,114 Z" fill="#f7a21b"/>
</svg>

<div class="abs" style="left:68px;top:4790px;display:flex;align-items:center;gap:10px;font-family:'Bodoni Moda',serif;font-weight:700;font-size:24px;color:var(--blue)"><span style="width:20px;height:20px;border-radius:50%;background:var(--orange)"></span>Coral Bay Pools</div>

<div class="abs" style="left:382px;top:4724px"><div class="foot-h">Quick Links</div></div>
<ul class="foot-list abs" style="left:382px;top:4788px">
  <li>About Us</li><li>Services</li><li>Free Estimate</li><li>Blog</li><li>Contact Us</li>
</ul>

<div class="abs" style="left:568px;top:4724px"><div class="foot-h">Contact Us</div></div>
<div class="contact-row" style="top:4792px"><span class="ic"><svg width="14" height="14" viewBox="0 0 24 24" fill="#fff"><path d="M6 2c2 0 4 5 4 6s-3 2-3 3c0 2 4 6 6 7 1 0 2-3 3-3s6 2 6 4-3 5-6 5C9 24 0 15 0 8c0-3 3-6 6-6z"/></svg></span><span>CALL US<br>(702) 555-0148</span></div>
<div class="contact-row" style="top:4846px"><span class="ic"><svg width="14" height="12" viewBox="0 0 14 12"><rect x="1" y="1" width="12" height="10" fill="none" stroke="#fff" stroke-width="1.6"/><path d="M1 1l6 5 6-5" fill="none" stroke="#fff" stroke-width="1.6"/></svg></span><span>EMAIL US<br>poolsolutions@coralbaypoolslv.com</span></div>
<div class="contact-row" style="top:4900px"><span class="ic"><svg width="12" height="16" viewBox="0 0 12 16"><path d="M6 0a6 6 0 0 1 6 6c0 4-6 10-6 10S0 10 0 6a6 6 0 0 1 6-6z" fill="#fff"/><circle cx="6" cy="6" r="2" fill="#0b5aa2"/></svg></span><span>Address line Dummy here<br>Address line dummy</span></div>

<div class="abs" style="left:939px;top:4724px"><div class="foot-h">Our Newsletter</div></div>
<p class="abs" style="left:939px;top:4792px;width:200px;font-size:13px;line-height:17px;color:#222">Subscribe our newsletter to get the latest news.</p>
<div class="abs" style="left:939px;top:4842px;width:194px;height:31px;background:#fff;border:1px solid #d5dde6"></div>
<div class="abs" style="left:939px;top:4893px;width:96px;height:27px;background:var(--blue);color:#fff;font-size:10px;font-weight:700;display:flex;align-items:center;justify-content:center">SUBSCRIBE</div>

<div class="bottom-bar abs"></div>
<p class="abs" style="left:68px;top:4998px;font-size:13px;color:#fff">©2018 Coral Bay Pools - Do not copy. All rights reserved.</p>
<span class="social" style="left:1012px"></span>
<span class="social" style="left:1044px"></span>
<span class="social" style="left:1076px"></span>
<span class="social" style="left:1108px"></span>

</body>
</html>
```